Tidewell Horizon Magazine need Logo desing and front page for 1 edittion

This is a new magazine that will be circulating in Panama. the magazine will run non for profit,will be mostly informative and few advertizers to cover printing costs.
the magaine will oncce every 2 or 3 month. we need to present it to the editors who will be aproving or diss aproving the project.

we need a Logo desing for the name of the magazine "Tidewell Horizon" and the "front cover desing for the first edition" it will be good if the designer can incude the designed format for the iner magazine, for us just to add in the artucles and the spaces for advertizing.

the magazine content will be articles by govenment energy sectors, gloval warming articles, articles in renewvable enery, university profesor talking or promoting new ideas or university advances, orientations, special edition on book or international articles about the subject on saving enerty, different sectors, world innovations in renewbable energy, and the companies who will advertize will be comapnies selling VORN products, companies offfering product and services on renewvable energy, Led product and systems companies etc...

Printing

```html
<!DOCTYPE html>
<html lang="en">
<head>
<meta charset="utf-8">
<title>Tidewell Horizon – Power, People, Profits</title>
<link rel="stylesheet" href="https://fonts.googleapis.com/css2?family=Quicksand:wght@300;500&family=Arimo:wght@400;700&display=swap">
<style>
  :root {
    --backdrop: #e9e9e9;
    --paper: #ffffff;
    --headline: #4b6b7b;
    --body-text: #3a3a3a;
    --meta-text: #6f6f6f;
    --url-text: #9a9a9a;
    --binding: #1e1e1e;
    --sky-top: #5f9fd6;
    --sky-low: #c9e0ef;
    --field-top: #6f8a3e;
    --field-low: #3f5a22;
  }
  * { margin: 0; padding: 0; box-sizing: border-box; }
  html, body { width: 1200px; height: 1000px; overflow: hidden; background: var(--backdrop); }
  body { position: relative; font-family: "Arimo", Arial, sans-serif; color: var(--body-text); }

  .spread { position: absolute; left: 30px; top: 128px; width: 1140px; height: 737px; background: var(--paper); }

  .page-left { position: absolute; left: 0; top: 0; width: 568px; height: 737px; }
  .folio { position: absolute; top: 30px; font-size: 10px; color: var(--meta-text); letter-spacing: 0.2px; text-transform: uppercase; }
  .folio b { color: #333; font-weight: 700; }
  .folio .sep { display: inline-block; margin: 0 6px; }
  .page-left .folio { left: 32px; }

  .headline { position: absolute; left: 32px; top: 66px; white-space: nowrap; font-family: "Quicksand", sans-serif; font-weight: 500; font-size: 62px; line-height: 62px; letter-spacing: 5px; color: var(--headline); text-transform: uppercase; transform: scaleX(0.82); transform-origin: left top; }

  .standfirst { position: absolute; left: 32px; top: 214px; width: 508px; font-size: 10.3px; line-height: 18.6px; color: #111; }
  .standfirst .dropcap { float: left; font-family: "Quicksand", sans-serif; font-weight: 500; font-size: 40px; line-height: 34px; color: var(--headline); margin: 1px 4px 0 0; }

  .column { position: absolute; width: 156px; font-size: 8.4px; line-height: 13.4px; }
  .column p + p { margin-top: 7px; }
  .col-1-top { left: 32px; top: 312px; }
  .col-2-top { left: 207px; top: 312px; }
  .col-1-bottom { left: 32px; top: 574px; }
  .col-2-bottom { left: 207px; top: 574px; }
  .col-3 { left: 383px; top: 312px; }

  .pull-quote { position: absolute; left: 32px; top: 424px; white-space: nowrap; font-family: "Quicksand", sans-serif; font-weight: 300; font-size: 24px; line-height: 30px; letter-spacing: 1.6px; color: var(--headline); }

  .site-url { position: absolute; left: 0; width: 568px; top: 688px; text-align: center; font-size: 8.5px; color: var(--url-text); }

  .binding { position: absolute; left: 566px; top: 0; }

  .page-right { position: absolute; left: 568px; top: 0; width: 572px; height: 737px; }
  .feature-photo { position: absolute; inset: 0; background: linear-gradient(180deg, var(--sky-top) 0%, #8dbde3 35%, var(--sky-low) 68%, #a9b59a 74%, var(--field-top) 80%, var(--field-low) 100%); }
  .page-right .folio { right: 32px; color: #5a6a78; }
</style>
</head>
<body>
  <article class="spread">
    <section class="page-left">
      <div class="folio"><b>4</b><span class="sep">|</span>Tidewell Horizon</div>

      <h1 class="headline">Power, People,<br>Profits</h1>

      <p class="standfirst"><span class="dropcap">W</span>ind, sun and water are reshaping how Panama powers its homes and businesses. This issue looks at the people building that change, the investments behind it and the profits that follow when clean energy becomes a shared project rather than a distant promise for the future of the isthmus. Across farms, towns and universities, new ideas are already at work.</p>

      <div class="column col-1-top">
        <p>Along the windy ridges of the interior, turbines now turn above grazing land. Farmers lease their fields, keep their herds and earn a steady income from every season of strong trade winds, year after year.</p>
      </div>
      <div class="column col-2-top">
        <p>Engineers say the grid was never designed for this kind of supply. Storage, smart meters and new transmission lines will be needed before clean power can reach every district on equal terms and fair prices.</p>
      </div>

      <blockquote class="pull-quote">“The path towards<br>sustainable energy<br>sources will be long and<br>sometimes difficult.”</blockquote>

      <div class="column col-1-bottom">
        <p>Local cooperatives show that small investors can share the returns, and community support grows fast.</p>
        <p>Banks are watching closely. Several now offer green loans for solar roofs and lighting.</p>
      </div>
      <div class="column col-2-bottom">
        <p>Critics warn that costs still fall unevenly. Rural households pay more per unit and often wait longer for connections. Planners answer that the next wave of projects is designed with those gaps in mind, pairing each wind park with local training, jobs and cheaper tariffs.</p>
      </div>
      <div class="column col-3">
        <p>The national energy secretariat has set a clear target: a much larger share of electricity from renewable sources within the next decade. To get there, it has opened auctions to private developers, simplified permits for rooftop solar and begun mapping the best sites for wind, from the Pacific coast to the central highlands. University teams are helping, testing new blade designs and measuring wind speeds over a full year before any turbine is placed.</p>
        <p>Their findings are shared openly with every developer.</p>
        <p>Investors see steady returns, and buyers see stable prices. Both need long contracts and clear rules that do not change after each election.</p>
        <p>The next step is skills. Technicians trained in Panama can maintain the parks and keep the earnings at home, in the towns that host the turbines. New courses start this year, and local firms are already hiring the first graduates.</p>
      </div>

      <div class="site-url">www.tidewell-horizon.com</div>
    </section>

    <svg class="binding" width="4" height="737" viewBox="0 0 4 737" aria-hidden="true">
      <line x1="2" y1="6" x2="2" y2="737" stroke="var(--binding)" stroke-width="3" stroke-dasharray="26 18"/>
    </svg>

    <section class="page-right">
      <div class="feature-photo" role="img" aria-label="Photo of a row of white wind turbines on a green hillside under a blue sky, with horses and cows grazing in the foreground"></div>
      <div class="folio">January 2014<span class="sep">|</span><b>5</b></div>
    </section>
  </article>
</body>
</html>
```